Tallowood building company Business card design

I need a business card design for my company. I have a logo but dont have business cards with our logo..

www.tallowoodbuildingco.com.au

The logo is on the website

I need the same details as this design I have attached. we have changed the logo and colours. just like the website

Building

```html
<!DOCTYPE html>
<html lang="en">
<head>
<meta charset="utf-8">
<title>Tallowood Building – Business Card</title>
<link rel="stylesheet" href="https://fonts.googleapis.com/css2?family=Cinzel:wght@400;600&family=Lato:wght@400&display=swap">
<style>
  :root {
    --backdrop: #e9e7e3;
    --card: #ffffff;
    --brand-blue: #0f86c2;
    --brand-blue-light: #2a9bd3;
    --accent-grey: #c3c4c8;
    --ink: #161616;
    --rule: #ffffff;
  }
  * { margin: 0; padding: 0; box-sizing: border-box; }
  html, body {
    width: 1200px; height: 793px; overflow: hidden;
    background: var(--backdrop);
  }
  .card {
    position: absolute; left: 100px; top: 96px;
    width: 1000px; height: 600px;
    background: var(--card);
    box-shadow: 0 8px 24px rgba(0,0,0,0.18);
    overflow: hidden;
    font-family: "Lato", Arial, sans-serif;
    color: var(--ink);
  }
  .card-shapes { position: absolute; inset: 0; }
  .brand {
    position: absolute; left: 64px; top: 70px;
    display: flex; align-items: center; gap: 18px;
  }
  .brand-square {
    width: 46px; height: 46px; background: var(--brand-blue);
  }
  .brand-name {
    font-family: "Cinzel", Georgia, serif; font-weight: 600;
    font-size: 40px; line-height: 1.05; letter-spacing: 2px;
    color: var(--brand-blue);
  }
  .person {
    position: absolute; right: 60px; top: 200px; text-align: right;
  }
  .person-name {
    font-family: "Cinzel", Georgia, serif; font-weight: 400;
    font-size: 34px; letter-spacing: 2px; color: var(--ink);
  }
  .person-role {
    font-size: 24px; color: var(--brand-blue); margin-top: 4px; letter-spacing: 1px;
  }
  .services {
    position: absolute; left: 40px; top: 372px;
    font-size: 22px; line-height: 1.25; color: var(--ink);
  }
  .contact-list {
    position: absolute; left: 440px; top: 366px;
    list-style: none; font-size: 24px; line-height: 1;
  }
  .contact-list li {
    display: flex; align-items: center; gap: 14px; height: 42px;
  }
  .contact-icon { width: 26px; height: 26px; flex: none; }
</style>
</head>
<body>
<main class="card" aria-label="Tallowood Building business card">
  <svg class="card-shapes" width="1000" height="600" viewBox="0 0 1000 600" aria-hidden="true">
    <defs>
      <linearGradient id="blueSweep" x1="0" y1="0" x2="1" y2="0">
        <stop offset="0" stop-color="var(--brand-blue)"/>
        <stop offset="1" stop-color="var(--brand-blue-light)"/>
      </linearGradient>
    </defs>
    <path class="grey-band" d="M0,316 C330,228 740,280 1000,548 L1000,600 L0,600 Z" fill="var(--accent-grey)"/>
    <path class="blue-band" d="M0,336 C330,252 720,300 945,600 L0,600 Z" fill="url(#blueSweep)"/>
    <line class="divider" x1="410" y1="370" x2="410" y2="560" stroke="var(--rule)" stroke-width="2"/>
  </svg>

  <div class="brand">
    <div class="brand-square"></div>
    <div class="brand-name">Tallowood<br>Building</div>
  </div>

  <div class="person">
    <div class="person-name">Marek Dolan</div>
    <div class="person-role">Director</div>
  </div>

  <p class="services">New Homes, Addition &amp; Renovation<br>Domestic &amp; Commercial Builders</p>

  <ul class="contact-list">
    <li>
      <svg class="contact-icon" viewBox="0 0 26 26" aria-hidden="true"><path d="M4 9 Q13 3 22 9 L20 12 L16 10 L16 8 Q13 7 10 8 L10 10 L6 12 Z M6 14 H20 L22 22 H4 Z" fill="#fff"/></svg>
      <span>9317 4260</span>
    </li>
    <li>
      <svg class="contact-icon" viewBox="0 0 26 26" aria-hidden="true"><rect x="7" y="2" width="12" height="22" rx="2" fill="none" stroke="#fff" stroke-width="2"/><circle cx="13" cy="20" r="1.3" fill="#fff"/></svg>
      <span>0412558903 (Marek)</span>
    </li>
    <li>
      <svg class="contact-icon" viewBox="0 0 26 26" aria-hidden="true"><rect x="2" y="5" width="22" height="16" fill="#fff"/><path d="M2 5 L13 14 L24 5" fill="none" stroke="var(--brand-blue)" stroke-width="1.6"/></svg>
      <span>info@tallowoodbuildingco.com.au</span>
    </li>
    <li>
      <svg class="contact-icon" viewBox="0 0 26 26" aria-hidden="true"><rect x="2" y="4" width="22" height="14" fill="none" stroke="#fff" stroke-width="2"/><path d="M9 23 H17 M13 18 V23" stroke="#fff" stroke-width="2"/></svg>
      <span>www.tallowoodbuildingco.com.au</span>
    </li>
  </ul>
</main>
</body>
</html>
```